Modern Verdell Tree Care Website

I need a website for a full service Tree Care company. The company provides tree pruning, tree removal, tree preservation, emergency services, stump grinding, and emergency tree services.

Target Market(s)

Customers that need tree services

Industry/Entity Type

Landscaping, Tree Services

Coding

Coded - Design and coding required

Number of Pages Required

5+ page

Font styles to use
Sans Serif

Requirements
Must have
• Good clean design that showcases the services the company provides.
Nice to have
• Services page; contact form, blog, home page, about page

```html
<!DOCTYPE html>
<html lang="en">
<head>
<meta charset="utf-8">
<title>Verdell Tree Care</title>
<link href="https://fonts.googleapis.com/css2?family=Open+Sans:wght@400;600;700;800&family=Roboto:wght@400;500;700&display=swap" rel="stylesheet">
<style>
:root{
  --green:#8cc63f;
  --slate:#4b6473;
  --slate-dark:#3f5663;
  --orange:#f7941d;
  --ink:#111;
  --muted:#666;
  --mint:#eef6e2;
  --white:#fff;
}
*{box-sizing:border-box;margin:0;padding:0}
html,body{width:1200px;height:3880px;overflow:hidden}
body{font-family:'Roboto',Arial,sans-serif;color:var(--ink);background:var(--white);position:relative}
.abs{position:absolute}
.heading{font-family:'Open Sans',Arial,sans-serif;font-weight:800;text-transform:uppercase;letter-spacing:.5px}
.heading .accent{color:var(--green)}
.btn{position:absolute;background:var(--slate);color:#fff;font:700 14px 'Roboto',Arial,sans-serif;display:flex;align-items:center;justify-content:center;text-transform:uppercase}

/* header */
.site-header{position:absolute;left:0;top:0;width:1200px;height:101px;background:#fff}
.brand{position:absolute;left:110px;top:24px;display:flex;align-items:center;gap:10px;font:800 26px 'Open Sans',sans-serif;color:var(--green)}
.brand .mark{width:34px;height:34px;background:var(--orange)}
.header-phone{position:absolute;left:923px;top:8px;display:flex;align-items:center;gap:10px;font:500 17px 'Roboto',sans-serif;color:#222}
.icon-box{width:32px;height:31px;background:var(--orange);display:flex;align-items:center;justify-content:center}
.nav-bar{position:absolute;left:376px;top:53px;width:824px;height:48px;background:var(--green);clip-path:polygon(26px 0,100% 0,100% 100%,0 100%)}
.nav-bar a{position:absolute;top:0;height:48px;line-height:48px;color:#fff;font:700 14px 'Roboto',sans-serif;text-decoration:none}
.nav-bar .cta{background:var(--slate);padding:0 19px}

/* hero */
.hero{position:absolute;left:0;top:101px;width:1200px;height:652px;background:radial-gradient(ellipse at 78% 45%,#8a5a3c 0%,#4a3125 28%,#2d211b 60%,#1c1613 100%)}
.hero-welcome{position:absolute;left:114px;top:180px;color:#fff;font:700 17px 'Roboto',sans-serif}
.hero-title{position:absolute;left:112px;top:218px;color:#fff;font-size:66px;line-height:1}
.hero-text{position:absolute;left:114px;top:320px;width:520px;color:#fff;font:400 17px/31px 'Roboto',sans-serif}
.dots{position:absolute;left:550px;top:598px;display:flex;gap:8px;align-items:center}
.dots span{width:4px;height:4px;border-radius:50%;background:#fff}
.dots .on{width:62px;height:4px;border-radius:2px}

/* about */
.about{position:absolute;left:0;top:753px;width:1200px;height:501px;background:#fff}
.about-photo{position:absolute;left:110px;top:78px;width:429px;height:339px;background:linear-gradient(135deg,#4d6b2f,#9cbf6a 45%,#6a5a48 75%,#3e5530)}
.about-title{position:absolute;left:698px;top:112px;font-size:50px}
.about-copy{position:absolute;left:698px;top:180px;width:400px;color:var(--muted);font:400 14px/25.5px 'Roboto',sans-serif}
.about-copy p+p{margin-top:14px}

/* services */
.services{position:absolute;left:0;top:1254px;width:1200px;height:731px;background:var(--mint)}
.section-title{position:absolute;left:0;width:1200px;text-align:center;font-size:50px}
.services-sub{position:absolute;left:280px;top:150px;width:640px;text-align:center;color:#555;font:400 14px/26px 'Open Sans',sans-serif}
.card{position:absolute;top:229px;width:259px;height:336px;overflow:hidden;color:#fff;text-align:center}
.card .fill{position:absolute;inset:0}
.card .shade{position:absolute;left:0;right:0;bottom:0;height:150px;background:linear-gradient(transparent,rgba(0,0,0,.75))}
.card .ico{position:absolute;left:112px;top:206px;width:34px;height:34px;border-radius:50%;background:var(--green);display:flex;align-items:center;justify-content:center}
.card h3{position:absolute;left:0;right:0;top:247px;font:700 14px 'Roboto',sans-serif;text-transform:uppercase}
.card p{position:absolute;left:20px;right:20px;top:272px;font:400 14px/25px 'Roboto',sans-serif}
.round-arrow{position:absolute;width:48px;height:48px;border-radius:50%;background:#fff;box-shadow:0 2px 6px rgba(0,0,0,.25);display:flex;align-items:center;justify-content:center}

/* why */
.why{position:absolute;left:0;top:1985px;width:1200px;height:479px;background:var(--slate)}
.why .section-title{color:#fff;top:92px}
.feature{position:absolute;top:196px;width:240px;text-align:center;color:#fff}
.feature svg{display:block;margin:0 auto}
.feature h3{margin-top:22px;font:500 17px 'Roboto',sans-serif;text-transform:uppercase}
.feature p{margin-top:14px;font:400 14px/26px 'Roboto',sans-serif}

/* testimonials */
.testimonials{position:absolute;left:0;top:2464px;width:1200px;height:556px;background:#fff}
.quote-card{position:absolute;left:193px;top:217px;width:816px;height:241px;background:#f1f1f1;border-radius:30px;text-align:center}
.quote-card h4{position:absolute;left:0;right:0;top:66px;font:500 14px 'Roboto',sans-serif}
.quote-card p{position:absolute;left:60px;right:60px;top:100px;color:#555;font:400 14px/31px 'Roboto',sans-serif}
.avatar{position:absolute;left:561px;top:177px;width:74px;height:74px;border-radius:50%;background:linear-gradient(#c9b9a8,#6d6f78);border:3px solid #fff}
.small-arrow{position:absolute;width:42px;height:42px;border-radius:50%;background:var(--slate);display:flex;align-items:center;justify-content:center}

/* contact */
.contact{position:absolute;left:0;top:3020px;width:1200px;height:515px;background:var(--mint)}
.field{position:absolute;background:#fff;color:#777;font:400 12px 'Roboto',sans-serif;padding:22px 18px}

/* footer */
.site-footer{position:absolute;left:0;top:3535px;width:1200px;height:345px;background:#050505;color:#fff}
.footer-brand{position:absolute;left:0;width:1200px;top:80px;display:flex;justify-content:center;align-items:center;gap:10px;font:800 28px 'Open Sans',sans-serif}
.footer-brand .mark{width:34px;height:34px;background:#fff}
.footer-nav a{position:absolute;top:168px;color:#fff;font:700 14px 'Roboto',sans-serif;text-decoration:none}
.footer-contact{position:absolute;top:214px;display:flex;align-items:center;gap:12px;font:700 17px 'Roboto',sans-serif}
.copyright{position:absolute;left:0;width:1200px;top:278px;text-align:center;font:400 10px 'Roboto',sans-serif}
</style>
</head>
<body>

<header class="site-header">
  <div class="brand"><span class="mark"></span>Verdell Tree Care</div>
  <div class="header-phone">
    <span class="icon-box"><svg width="16" height="16" viewBox="0 0 24 24"><path fill="#fff" d="M6.6 10.8a15 15 0 0 0 6.6 6.6l2.2-2.2c.3-.3.7-.4 1-.2 1.1.4 2.3.6 3.6.6.6 0 1 .4 1 1V20c0 .6-.4 1-1 1A17 17 0 0 1 3 4c0-.6.4-1 1-1h3.5c.6 0 1 .4 1 1 0 1.3.2 2.5.6 3.6.1.3 0 .7-.2 1z"/></svg></span>
    (555) 014 - 2739
  </div>
  <nav class="nav-bar">
    <a style="left:68px">HOME</a>
    <a style="left:156px">ABOUT</a>
    <a style="left:251px">SERVICES</a>
    <a style="left:358px">BLOG</a>
    <a style="left:443px">CONTACT</a>
    <a class="cta" style="left:535px">GET A FREE ESTIMATE</a>
  </nav>
</header>

<section class="hero" role="img" aria-label="Hands cupping a seedling growing in dark soil">
  <div class="hero-welcome">WELCOME TO</div>
  <h1 class="hero-title heading">Verdell <span class="accent">Tree</span> Care</h1>
  <p class="hero-text">Lorem ipsum dolor sit amet, consectetur adipiscing elit, sed do eiusmod tempor incididunt ut labore et dolore</p>
  <div class="btn" style="left:114px;top:406px;width:181px;height:43px">Get Started</div>
  <div class="dots"><span class="on"></span><span></span><span></span><span></span></div>
</section>

<section class="about">
  <div class="about-photo" role="img" aria-label="Arborist in helmet holding a chainsaw in a forest"></div>
  <h2 class="about-title heading"><span class="accent">About</span> Us</h2>
  <div class="about-copy">
    <p>Sed ut perspiciatis unde omnis iste natus error sit voluptatem accusantium doloremque laudantium, totam rem aperiam, eaque ipsa quae ab illo inventore veritatis et quasi architecto beatae vitae dicta sunt explicabo. Nemo enim ipsam</p>
    <p>Sed ut perspiciatis unde omnis iste natus error sit voluptatem accusantium doloremque laudantium,</p>
  </div>
  <div class="btn" style="left:698px;top:369px;width:181px;height:41px">View More</div>
</section>

<section class="services">
  <h2 class="section-title heading" style="top:78px"><span class="accent">Our</span> Services</h2>
  <p class="services-sub">Lorem ipsum dolor sit amet, consectetur adipiscing elit, sed do eiusmod tempor incididunt ut labore et dolore magna aliqua. Ut enim ad minim</p>

  <div class="card" style="left:60px">
    <div class="fill" role="img" aria-label="Workers clearing fallen trees" style="background:linear-gradient(#c7cbcf,#7f7a5e 55%,#4a3f30)"></div>
    <div class="shade"></div>
    <div class="ico"><svg width="18" height="18" viewBox="0 0 24 24"><path fill="none" stroke="#fff" stroke-width="2" d="M12 21s-8-5-8-11a5 5 0 0 1 8-3 5 5 0 0 1 8 3c0 6-8 11-8 11z"/></svg></div>
    <h3>Emergency Services</h3>
    <p>Sed ut perspiciatis unde omnis iste natus error sit</p>
  </div>
  <div class="card" style="left:334px">
    <div class="fill" role="img" aria-label="Man pruning branches with loppers" style="background:linear-gradient(#dfe3e6,#9aa3a0 50%,#3f5060)"></div>
    <div class="shade"></div>
    <div class="ico"><svg width="18" height="18" viewBox="0 0 24 24"><path fill="none" stroke="#fff" stroke-width="2" d="M5 19L19 5M9 19l10-10"/></svg></div>
    <h3>Tree Pruning</h3>
    <p>Sed ut perspiciatis unde omnis iste natus error sit</p>
  </div>
  <div class="card" style="left:608px">
    <div class="fill" role="img" aria-label="Chainsaw cutting a log on grass" style="background:linear-gradient(#6f7c5a,#6fa040 45%,#2e3a22)"></div>
    <div class="shade"></div>
    <div class="ico"><svg width="18" height="18" viewBox="0 0 24 24"><circle cx="12" cy="10" r="6" fill="none" stroke="#fff" stroke-width="2"/><path stroke="#fff" stroke-width="2" d="M12 16v5"/></svg></div>
    <h3>Tree Removal</h3>
    <p>Sed ut perspiciatis unde omnis iste natus error sit</p>
  </div>
  <div class="card" style="left:881px">
    <div class="fill" role="img" aria-label="Gloved hands planting a young sapling" style="background:linear-gradient(#a8b98a,#6a8d3c 45%,#3a3325)"></div>
    <div class="shade"></div>
    <div class="ico"><svg width="18" height="18" viewBox="0 0 24 24"><path fill="none" stroke="#fff" stroke-width="2" d="M12 20v-8M12 12c0-4 3-6 7-6 0 4-3 6-7 6zM12 14c0-3-2-5-6-5 0 3 2 5 6 5z"/></svg></div>
    <h3>Tree Preservation</h3>
    <p>Sed ut perspiciatis unde omnis iste natus error sit</p>
  </div>

  <div class="round-arrow" style="left:36px;top:369px"><svg width="14" height="14" viewBox="0 0 24 24"><path fill="none" stroke="#222" stroke-width="3" d="M15 4l-8 8 8 8"/></svg></div>
  <div class="round-arrow" style="left:1116px;top:369px"><svg width="14" height="14" viewBox="0 0 24 24"><path fill="none" stroke="#222" stroke-width="3" d="M9 4l8 8-8 8"/></svg></div>
  <div class="btn" style="left:510px;top:600px;width:181px;height:42px">View More</div>
</section>

<section class="why">
  <h2 class="section-title heading"><span style="color:#fff">Why</span> <span class="accent">Choose</span> Us</h2>
  <div class="feature" style="left:103px">
    <svg width="62" height="64" viewBox="0 0 62 64" fill="none" stroke="#fff" stroke-width="2"><rect x="6" y="4" width="38" height="54" rx="2"/><path d="M14 16h22M14 24h22M14 32h14M14 40h12"/><circle cx="46" cy="40" r="9"/><path d="M41 48l-2 12 7-4 7 4-2-12"/></svg>
    <h3>Licensed &amp; Insured</h3>
    <p>Lorem ipsum dolor sit amet,<br>consectetur adipiscing</p>
  </div>
  <div class="feature" style="left:353px">
    <svg width="62" height="64" viewBox="0 0 62 64" fill="none" stroke="#fff" stroke-width="2"><circle cx="31" cy="24" r="18"/><circle cx="31" cy="24" r="11"/><path d="M31 17l2.2 4.6 5 .6-3.7 3.4 1 5-4.5-2.5-4.5 2.5 1-5-3.7-3.4 5-.6z"/><path d="M20 38l-6 20 8-3 5 6 4-15M42 38l6 20-8-3-5 6-4-15"/></svg>
    <h3>Proffessional</h3>
    <p>Lorem ipsum dolor sit amet,<br>consectetur adipiscing</p>
  </div>
  <div class="feature" style="left:606px">
    <svg width="62" height="70" viewBox="0 0 62 70" fill="none" stroke="#fff" stroke-width="2"><path d="M20 4h22l-4 12H24z"/><rect x="8" y="16" width="46" height="50" rx="23"/><text x="31" y="40" fill="#fff" stroke="none" font-family="Roboto,sans-serif" font-size="12" font-weight="700" text-anchor="middle">TAX</text><path d="M31 46v14M26 55l5 5 5-5"/></svg>
    <h3>Free&nbsp; Estimate</h3>
    <p>Lorem ipsum dolor sit amet,<br>consectetur adipiscing</p>
  </div>
  <div class="feature" style="left:857px">
    <svg width="68" height="64" viewBox="0 0 68 64" fill="none" stroke="#fff" stroke-width="2"><path d="M22 30s-10-10-10-17a10 10 0 0 1 20 0c0 7-10 17-10 17z"/><circle cx="22" cy="13" r="4"/><path d="M44 46s-10-10-10-17a10 10 0 0 1 20 0c0 7-10 17-10 17z"/><circle cx="44" cy="29" r="4"/><path d="M6 40l14 10 12-6 14 14 16-6"/></svg>
    <h3>Locally Owned</h3>
    <p>Lorem ipsum dolor sit amet,<br>consectetur adipiscing</p>
  </div>
</section>

<section class="testimonials">
  <h2 class="section-title heading" style="top:76px"><span class="accent">Our</span> Testimonials</h2>
  <div class="quote-card">
    <h4>DANA WHITFIELD</h4>
    <p>I would highly recommend Brightline for SEO and Clearview Marketing. We have seen huge improvement in our rankings since partnering with them. Marla Quinn is a tremendous asset to your organization. Thank you Marla and Brightline for being a great partner!</p>
  </div>
  <div class="avatar" role="img" aria-label="Customer portrait"></div>
  <div class="small-arrow" style="left:172px;top:316px"><svg width="10" height="10" viewBox="0 0 24 24"><path fill="none" stroke="#fff" stroke-width="4" d="M15 4l-8 8 8 8"/></svg></div>
  <div class="small-arrow" style="left:985px;top:316px"><svg width="10" height="10" viewBox="0 0 24 24"><path fill="none" stroke="#fff" stroke-width="4" d="M9 4l8 8-8 8"/></svg></div>
</section>

<section class="contact">
  <h2 class="section-title heading" style="top:76px"><span class="accent">Contact</span> Us</h2>
  <div class="field" style="left:245px;top:155px;width:332px;height:66px">Name</div>
  <div class="field" style="left:245px;top:230px;width:332px;height:66px">Phone</div>
  <div class="field" style="left:245px;top:305px;width:332px;height:66px">Email</div>
  <div class="field" style="left:587px;top:155px;width:368px;height:216px">Message</div>
  <div class="btn" style="left:510px;top:390px;width:181px;height:42px">Submit</div>
</section>

<footer class="site-footer">
  <div class="footer-brand"><span class="mark"></span>Verdell Tree Care</div>
  <nav class="footer-nav">
    <a style="left:383px">HOME</a>
    <a style="left:471px">ABOUT</a>
    <a style="left:565px">SERVICES</a>
    <a style="left:673px">BLOG</a>
    <a style="left:757px">CONTACT</a>
  </nav>
  <div class="footer-contact" style="left:366px">
    <span class="icon-box"><svg width="16" height="16" viewBox="0 0 24 24"><path fill="#fff" d="M6.6 10.8a15 15 0 0 0 6.6 6.6l2.2-2.2c.3-.3.7-.4 1-.2 1.1.4 2.3.6 3.6.6.6 0 1 .4 1 1V20c0 .6-.4 1-1 1A17 17 0 0 1 3 4c0-.6.4-1 1-1h3.5c.6 0 1 .4 1 1 0 1.3.2 2.5.6 3.6.1.3 0 .7-.2 1z"/></svg></span>
    (555) 014 - 2739
  </div>
  <div class="footer-contact" style="left:595px">
    <span class="icon-box"><svg width="16" height="14" viewBox="0 0 24 18"><rect x="1" y="1" width="22" height="16" fill="#fff"/><path d="M1 1l11 9 11-9" fill="none" stroke="#f7941d" stroke-width="2"/></svg></span>
    info@verdelltreecare.com
  </div>
  <div class="copyright">COPYRIGHT@2024 - ALL RIGHTS BY VERDELL TREE CARE</div>
</footer>

</body>
</html>
```